Redesign This Psychology Website

We would like a slight redesign of this successful psychology (relationship counselling) website:

www.TheKelvaleClinic.com.au

We are updating the website, and we'd like a slight refresh of the design and style.

Please keep to very similar colours, and use the same logo. We're looking for around 10 page templates, however the main one is the home page.

Keep in mind, this website already converts quite well, so we want a new, fresh design in keeping with this one. Please don't bother designing something too extremely different.

thanks :)

Target Market(s)

couples who are looking for relationship counselling. Men and women, 25 - 70, across Australia

Industry/Entity Type

Psychology

Number of Pages Required

5+ page

Font styles to use
Sans Serif

Colors
87cfc6
b7a5cd
ec1f27
ffffff
cee9f5

Requirements
Must have
• a similar look to the current design, just looking for a slight refresh.
• Search bar
• Areas for lots of photos
• same logo
• lots of content areas
Nice to have
• great content areas, where we can display a lot of content and our areas.
Should not have
• no colors like orange, etc.
• should not have a totally different feel.

```html
<!DOCTYPE html>
<html lang="en">
<head>
<meta charset="utf-8">
<title>Kelvale Clinic – Relationship &amp; Marriage Counselling</title>
<link rel="stylesheet" href="https://fonts.googleapis.com/css2?family=Raleway:wght@400;500;600&family=Open+Sans:wght@400;600&display=swap">
<style>
:root{
  --teal:#87cfc6;
  --teal-dark:#5bbab0;
  --lilac:#b7a5cd;
  --lilac-dark:#a08cbf;
  --red:#ec1f27;
  --white:#ffffff;
  --sky:#e6f3f9;
  --ink:#2b2b2b;
  --grey:#777;
  --line:#dcdcdc;
  --bar:#f1f1f1;
}
*{box-sizing:border-box;margin:0;padding:0}
html,body{width:1200px;height:3358px;overflow:hidden}
body{background:var(--white);font-family:"Open Sans",sans-serif;color:var(--ink);position:relative}
a{color:inherit;text-decoration:none}
.heading{font-family:"Raleway",sans-serif}

/* top bar */
.top-bar{height:40px;background:var(--bar);border-bottom:1px solid var(--line);display:flex;justify-content:space-between;align-items:center;padding:0 128px 0 145px;font-size:13px;color:#666}
.top-links{display:flex;height:40px}
.top-links a{padding:0 14px;border-left:1px solid var(--line);line-height:40px}

/* header */
.site-header{height:121px;display:flex;align-items:center;padding:0 128px;position:relative}
.brand{display:flex;align-items:center;gap:12px}
.brand-dot{width:44px;height:44px;border-radius:50%;background:var(--teal)}
.brand-name{font-family:"Raleway",sans-serif;font-size:34px;font-weight:500;color:var(--teal-dark);line-height:1}
.search{position:absolute;left:470px;top:44px;width:354px;height:38px;border:1px solid var(--line);display:flex;align-items:center;padding-left:12px;gap:8px;font-size:13px;color:#999}
.call{position:absolute;right:128px;top:36px;text-align:right}
.call-label{font-size:15px;color:var(--teal-dark)}
.call-number{font-family:"Raleway",sans-serif;font-size:24px;font-weight:600;color:var(--teal-dark);display:flex;align-items:center;gap:6px}

/* nav */
.main-nav{height:70px;background:linear-gradient(180deg,#9bd8d0,var(--teal));display:flex;padding-left:128px}
.main-nav a{color:var(--white);font-family:"Raleway",sans-serif;font-weight:600;font-size:16px;line-height:17px;text-transform:uppercase;padding:0 14px;display:flex;align-items:center;border-right:1px solid rgba(255,255,255,.5)}
.main-nav a:first-child{padding-left:6px}

/* hero */
.hero{position:relative;height:510px}
.hero-photo{position:absolute;inset:0;background:linear-gradient(100deg,#5f7d3a 0%,#a9b86a 35%,#e9d9c2 55%,#d7c8a3 75%,#6f8a48 100%)}
.hero-title{position:absolute;left:130px;top:262px;color:var(--white);font-family:"Raleway",sans-serif;font-weight:600;font-size:37px;line-height:50px;text-transform:uppercase}
.finder{position:absolute;left:768px;top:87px;width:295px;height:360px;background:rgba(183,165,205,.93);padding:22px 24px;color:var(--white)}
.finder h2{font-family:"Raleway",sans-serif;font-weight:600;font-size:22px;text-align:center;line-height:28px;margin-bottom:20px}
.finder label{display:block;font-size:12px;margin-bottom:5px}
.finder .field{height:33px;background:var(--white);margin-bottom:18px;font-size:12px;color:#888;display:flex;align-items:center;justify-content:space-between;padding:0 10px}
.finder .btn{height:38px;background:var(--red);display:flex;align-items:center;justify-content:center;font-weight:600;font-size:15px;margin-top:4px}
.dots{position:absolute;left:558px;top:466px;display:flex;gap:10px}
.dots span{width:12px;height:12px;border-radius:50%;background:var(--white)}
.dots span:first-child{background:transparent;border:2px solid var(--white)}

/* intro */
.intro{position:relative;height:390px}
.video{position:absolute;left:132px;top:56px;width:434px;height:273px;background:linear-gradient(120deg,#a8b7b8,#d8c9bd 50%,#b89c8a);border:3px solid #eee}
.play{position:absolute;left:183px;top:103px}
.intro-text{position:absolute;left:609px;top:66px;width:460px}
.intro-text h1{font-weight:500;font-size:31px;line-height:36px;margin-bottom:26px}
.intro-text p{font-size:14px;line-height:27px;color:var(--grey)}
.divider{position:absolute;left:132px;top:390px;width:936px;height:1px;background:var(--line)}
.divider::after{content:"";position:absolute;left:456px;top:-1px;width:16px;height:16px;background:var(--white);border-right:1px solid var(--line);border-bottom:1px solid var(--line);transform:rotate(45deg)}

/* services */
.services{position:absolute;top:1182px;left:132px;display:flex;gap:11px}
.service{width:225px;height:341px;border:1px solid var(--line);position:relative}
.service-photo{height:161px}
.service-body{padding:16px 18px}
.service h3{font-family:"Raleway",sans-serif;font-weight:500;font-size:19px;line-height:23px;margin-bottom:10px}
.service p{font-size:11px;line-height:15px;color:#888}
.more-btn{position:absolute;left:18px;bottom:22px;display:inline-block;background:var(--lilac);color:var(--white);font-size:11px;font-weight:600;padding:8px 18px}

/* psychologists band */
.issues{position:absolute;top:1581px;left:0;width:1200px;height:463px;overflow:hidden}
.issues-photo{position:absolute;inset:0;background:linear-gradient(90deg,#d8c5b2,#c9b8a5 50%,#9fb3bc)}
.issues-panel{position:absolute;inset:0;background:linear-gradient(135deg,var(--lilac) 0%,#a9b8cf 50%,var(--teal) 100%);clip-path:polygon(0 0,784px 0,578px 100%,0 100%)}
.issues-panel h2{position:absolute;left:132px;top:64px;color:var(--white);font-weight:500;font-size:31px}
.issues-panel .lead{position:absolute;left:132px;top:108px;color:var(--white);font-size:16px}
.issue-list{position:absolute;top:160px;list-style:none;color:var(--white);font-size:14px}
.issue-list li{height:33.5px}
.issue-list li::before{content:"›";margin-right:10px}
.col-a{left:138px}.col-b{left:350px}

/* photos */
.photos{position:absolute;top:2044px;left:0;width:1200px;height:479px;background:var(--sky)}
.photos h2{text-align:center;font-weight:500;font-size:31px;margin-top:50px}
.photo-grid{position:absolute;left:137px;top:103px;width:926px;height:309px;display:grid;grid-template-columns:201px 180px 180px 180px 177px;grid-template-rows:1fr 1fr;gap:3px}
.photo-grid div:nth-child(1){grid-row:1/3}
.photo-grid div:nth-child(2){grid-column:2/4}
.photo-grid div:nth-child(7){grid-column:4/6}

/* blog */
.blogs{position:absolute;top:2523px;left:0;width:1200px;height:470px}
.blogs h2{position:absolute;left:132px;top:40px;color:var(--red);font-weight:500;font-size:31px}
.post{position:absolute;top:99px;width:294px}
.post-photo{height:177px;position:relative}
.date{position:absolute;left:0;bottom:-22px;width:58px;height:58px;background:var(--teal);color:var(--white);text-align:center;font-size:24px;line-height:26px;padding-top:5px}
.date small{display:block;font-size:11px;line-height:12px}
.post h3{font-family:"Raleway",sans-serif;font-weight:600;font-size:15px;margin:34px 0 0 12px}
.post p{font-size:12px;line-height:20px;color:#999;margin:10px 12px 0}
.post .read{display:block;color:var(--teal-dark);font-size:12px;margin:8px 12px 0}

/* footer */
.site-footer{position:absolute;top:2993px;left:0;width:1200px;height:298px;background:linear-gradient(180deg,#e6e6e6 0,#f7f7f7 30px,#f7f7f7)}
.site-footer .brand{position:absolute;left:132px;top:68px}
.foot-col{position:absolute;top:60px;font-size:12px;color:#555}
.foot-col h4{font-family:"Raleway",sans-serif;font-weight:600;font-size:15px;color:var(--teal-dark);margin-bottom:14px}
.foot-col li{list-style:none;line-height:28px}
.social{display:flex;gap:8px;margin-top:10px}
.social span{width:30px;height:30px;border-radius:50%;background:var(--teal)}
.copyright{position:absolute;top:3291px;left:0;width:1200px;height:67px;background:#ececec;text-align:center;font-size:12px;color:#777;line-height:50px}
</style>
</head>
<body>

<div class="top-bar">
  <a href="#">Join Our Associate Program →</a>
  <nav class="top-links"><a href="#">Home</a><a href="#">Cart</a><a href="#">Blog</a><a href="#">Resources</a><a href="#" style="border-right:1px solid var(--line)">Contact</a></nav>
</div>

<header class="site-header">
  <div class="brand">
    <span class="brand-dot"></span>
    <div class="brand-name">Kelvale Clinic</div>
  </div>
  <div class="search">
    <svg width="14" height="14" viewBox="0 0 14 14"><circle cx="6" cy="6" r="4.5" fill="none" stroke="#999" stroke-width="1.5"/><path d="M9.5 9.5 13 13" stroke="#999" stroke-width="1.5"/></svg>
    Search here
  </div>
  <div class="call">
    <div class="call-label">Call Us Now</div>
    <div class="call-number"><svg width="22" height="22" viewBox="0 0 24 24"><path d="M6.6 10.8a15 15 0 0 0 6.6 6.6l2.2-2.2c.3-.3.7-.4 1-.2 1.1.4 2.3.6 3.6.6.6 0 1 .4 1 1V20c0 .6-.4 1-1 1A17 17 0 0 1 3 4c0-.6.4-1 1-1h3.5c.6 0 1 .4 1 1 0 1.3.2 2.5.6 3.6.1.3 0 .7-.2 1z" fill="none" stroke="var(--red)" stroke-width="1.8"/></svg>1300 555 014</div>
  </div>
</header>

<nav class="main-nav">
  <a href="#">Counselling<br>Types</a>
  <a href="#">Relationship Counselling<br>Locations</a>
  <a href="#">Sex Therapy<br>Locations</a>
  <a href="#">About Us</a>
  <a href="#">Quizzes</a>
  <a href="#">FAQ'S</a>
  <a href="#" style="border-right:0">Contact</a>
</nav>

<section class="hero">
  <div class="hero-photo" role="img" aria-label="Happy couple embracing outdoors among sunlit trees"></div>
  <h2 class="hero-title">Relationship &amp;<br>Marriage Counselling</h2>
  <form class="finder">
    <h2>Find Our Psychologist<br>Near You</h2>
    <label>Type of Counselling</label>
    <div class="field">Select <svg width="10" height="6" viewBox="0 0 10 6"><path d="M1 1l4 4 4-4" fill="none" stroke="#888" stroke-width="1.4"/></svg></div>
    <label>Location</label>
    <div class="field"></div>
    <label>Postcode</label>
    <div class="field"></div>
    <div class="btn">SEARCH</div>
  </form>
  <div class="dots"><span></span><span></span><span></span><span></span></div>
</section>

<section class="intro">
  <div class="video" role="img" aria-label="Video still of a psychologist speaking">
    <svg class="play" width="72" height="72" viewBox="0 0 72 72"><circle cx="36" cy="36" r="34" fill="none" stroke="#fff" stroke-width="2"/><path d="M29 23v26l21-13z" fill="#fff"/></svg>
  </div>
  <div class="intro-text">
    <h1 class="heading">We Specialise in Relationship<br>&amp; Marriage Counselling</h1>
    <p>At the Kelvale Clinic, we are a group of PSYCHOLOGISTS, Australia wide who are passionate about relationships and helping you with yours. Our vision is to provide the most highly regarded and comprehensive marriage counselling and relationship counselling, and sex therapy in Australia, at reasonable and affordable rates.</p>
  </div>
  <div class="divider"></div>
</section>

<section class="services">
  <article class="service">
    <div class="service-photo" role="img" aria-label="Couple talking with a counsellor" style="background:linear-gradient(135deg,#c9b7a6,#e6dcd2)"></div>
    <div class="service-body"><h3>Relationship<br>Counselling</h3><p>Communication, Recovering from an affair, Loss of intimacy &amp; love, Power battles, Feeling</p></div>
    <a class="more-btn" href="#">Learn More</a>
  </article>
  <article class="service">
    <div class="service-photo" role="img" aria-label="Couple's feet under bed sheets" style="background:linear-gradient(135deg,#e9d8cf,#f5ece8)"></div>
    <div class="service-body"><h3>Sex Therapy<br>Counselling</h3><p>Low libido , Erectile difficulties, Premature ejaculation, Differing libidos, Porn addiction</p></div>
    <a class="more-btn" href="#">Learn More</a>
  </article>
  <article class="service">
    <div class="service-photo" role="img" aria-label="Couple arguing on a sofa" style="background:linear-gradient(135deg,#b9a89a,#ddd2c8)"></div>
    <div class="service-body"><h3>Anger Management<br>Counselling</h3><p>Managing angry outbursts, expressing your anger in healthy ways</p></div>
    <a class="more-btn" href="#">Learn More</a>
  </article>
  <article class="service">
    <div class="service-photo" role="img" aria-label="Portrait of a man in three poses" style="background:linear-gradient(135deg,#6e5d4f,#a89280)"></div>
    <div class="service-body"><h3>Narcissism<br>Conselling</h3><p>Managing narcissistic, superior, entitled, arrogant and lack of empathy tendencies</p></div>
    <a class="more-btn" href="#">Learn More</a>
  </article>
</section>

<section class="issues">
  <div class="issues-photo" role="img" aria-label="Smiling mature couple by the sea"></div>
  <div class="issues-panel">
    <h2 class="heading">Our Kelvale Relationship Psychologists</h2>
    <p class="lead">Here are some of the common ones:</p>
    <ul class="issue-list col-a"><li>Affairs</li><li>Controlling behaviour</li><li>Verbal abuse</li><li>Imbalance of power</li><li>Lack of intimacy</li><li>Poor communication</li><li>Loss of love</li></ul>
    <ul class="issue-list col-b"><li>Relationship neglect</li><li>Sexual problems</li><li>Problems from childhood</li><li>Problems with parenting your children</li><li>Step children and in-laws</li><li>All forms of family problems</li><li>Anger management problems</li></ul>
  </div>
</section>

<section class="photos">
  <h2 class="heading">Our Photos</h2>
  <div class="photo-grid">
    <div role="img" aria-label="Stressed woman holding her head" style="background:linear-gradient(160deg,#6a6a6a,#9a9a9a)"></div>
    <div role="img" aria-label="Smiling couple together" style="background:linear-gradient(160deg,#c8d6dc,#e8ddd2)"></div>
    <div role="img" aria-label="Couple making a heart with their hands" style="background:linear-gradient(160deg,#c79a6a,#e6c9a1)"></div>
    <div role="img" aria-label="Couple in conversation" style="background:linear-gradient(160deg,#8a7566,#c2b1a3)"></div>
    <div role="img" aria-label="Laughing couple close together" style="background:linear-gradient(160deg,#b89a86,#e2d2c5)"></div>
    <div role="img" aria-label="Couple sharing a quiet moment" style="background:linear-gradient(160deg,#8c7a6c,#c9b8a8)"></div>
    <div role="img" aria-label="Family with a young child at home" style="background:linear-gradient(160deg,#d8cbb8,#f0e8dc)"></div>
  </div>
</section>

<section class="blogs">
  <h2 class="heading">Latest Blogs</h2>
  <article class="post" style="left:132px">
    <div class="post-photo" role="img" aria-label="Clasped hands" style="background:linear-gradient(135deg,#cbb8a6,#efe6dc)"><div class="date">02<small>APR</small></div></div>
    <h3>Your Blog Tittle here</h3>
    <p>Class aptent taciti sociosqu ad litora torquent per conubia nostra per inceptos hymenaeos Proin nulla arcu</p>
    <a class="read" href="#">Read More</a>
  </article>
  <article class="post" style="left:450px">
    <div class="post-photo" role="img" aria-label="Upset couple sitting apart" style="background:linear-gradient(135deg,#5d5049,#9a8a7e)"><div class="date">02<small>APR</small></div></div>
    <h3>Your Blog Tittle here</h3>
    <p>Class aptent taciti sociosqu ad litora torquent per conubia nostra per inceptos hymenaeos Proin nulla arcu</p>
    <a class="read" href="#">Read More</a>
  </article>
  <article class="post" style="left:766px">
    <div class="post-photo" role="img" aria-label="Couple in a counselling session" style="background:linear-gradient(135deg,#6f6a64,#b2aaa1)"><div class="date">02<small>APR</small></div></div>
    <h3>Your Blog Tittle here</h3>
    <p>Class aptent taciti sociosqu ad litora torquent per conubia nostra per inceptos hymenaeos Proin nulla arcu</p>
    <a class="read" href="#">Read More</a>
  </article>
</section>

<footer class="site-footer">
  <div class="brand">
    <span class="brand-dot"></span>
    <div class="brand-name">Kelvale Clinic</div>
  </div>
  <div class="foot-col" style="left:452px"><h4>QUICK LINKS</h4><ul><li>Home</li><li>About Us</li><li>Our Blogs</li><li>Shop Cart</li><li>Contact Us</li></ul></div>
  <div class="foot-col" style="left:620px"><h4>RESOURCES</h4><ul><li>Counselling Type</li><li>Sex Therapy</li><li>Quizzes</li><li>FAQ</li><li>Relationship Counselling</li></ul></div>
  <div class="foot-col" style="left:824px"><h4>CONTACT US</h4><ul><li>214 Harbour Lane Suite 12</li><li>1300 555 014</li><li>Email: info@kelvaleclinic.com.au</li></ul>
    <div class="social"><span></span><span></span><span></span><span></span></div>
  </div>
</footer>

<div class="copyright">© 2017 Company Name  All right reserved</div>

</body>
</html>
```